Business Card and Letterhead for Pimlu - modern real estate business

I need a double sided business card design for Pimlu. Please see business card brief here https://files.trelvonadocs.com/sheet/r/7QzTmWbaXLJnoPEd-kRyUgFhHsstbvCe2qfoMxDa_pz/view?mode=shared

Please feel free to design the business cards however you feel best. I am happy to give some creative freedoms and then provide feedback from there.

Please then also create a letterhead to match the business card design

Colors

Designer to choose colors to be used in the design.

Requirements
Must have
• Must be a modern, elegant business card which looks very professional

```html
<!DOCTYPE html>
<html lang="en">
<head>
<meta charset="utf-8">
<title>Pimlu Business Card</title>
<link href="https://fonts.googleapis.com/css2?family=Montserrat:wght@400;500;600;700&display=swap" rel="stylesheet">
<style>
  :root {
    --stage: #1c1c1c;
    --stage-light: #2e2e2e;
    --ink: #0a0a0a;
    --paper: #ffffff;
    --brand-red: #e3262e;
    --text-dark: #1a1a1a;
    --text-light: #ffffff;
  }
  * { box-sizing: border-box; margin: 0; padding: 0; }
  html, body {
    width: 1200px; height: 900px; overflow: hidden;
  }
  body {
    background: radial-gradient(ellipse at 50% 30%, var(--stage-light), var(--stage) 70%);
    font-family: "Montserrat", sans-serif;
    position: relative;
  }
  .card {
    position: absolute;
    left: 250px;
    width: 700px;
    height: 400px;
    overflow: hidden;
    box-shadow: 0 10px 30px rgba(0,0,0,0.55);
  }
  /* Back side */
  .card-back {
    top: 40px;
    background: var(--ink);
  }
  .card-back .wordmark {
    position: absolute;
    left: 0; right: 0; top: 130px;
    text-align: center;
    font-size: 96px;
    font-weight: 700;
    letter-spacing: 6px;
    color: var(--brand-red);
  }
  .card-back .site {
    position: absolute;
    left: 0; right: 0; bottom: 34px;
    text-align: center;
    font-size: 16px;
    font-weight: 500;
    letter-spacing: 1.5px;
    color: var(--text-light);
  }
  .card-back .site .accent { color: var(--brand-red); font-weight: 600; }

  /* Front side */
  .card-front {
    top: 460px;
    background: var(--paper);
  }
  .card-front .backdrop {
    position: absolute; inset: 0;
  }
  .card-front .wordmark {
    position: absolute;
    left: 44px; top: 30px;
    font-size: 46px;
    font-weight: 700;
    letter-spacing: 3px;
    color: var(--brand-red);
  }
  .agent {
    position: absolute;
    left: 44px; top: 118px;
  }
  .agent::before {
    content: "";
    position: absolute;
    left: -44px; top: 2px;
    width: 8px; height: 34px;
    background: var(--brand-red);
  }
  .agent-name {
    font-size: 24px;
    font-weight: 500;
    letter-spacing: 1.5px;
    color: var(--brand-red);
    line-height: 1.1;
  }
  .agent-title {
    font-size: 15px;
    font-weight: 500;
    color: var(--text-dark);
    margin-top: 2px;
  }
  .contact-list {
    position: absolute;
    left: 44px; top: 200px;
    list-style: none;
  }
  .contact-list li {
    display: flex;
    align-items: center;
    gap: 14px;
    font-size: 17px;
    font-weight: 500;
    color: var(--text-dark);
    line-height: 26px;
    letter-spacing: 0.5px;
  }
  .contact-list svg { width: 15px; height: 15px; flex: none; }
  .address {
    position: absolute;
    left: 44px; top: 306px;
    font-size: 17px;
    font-weight: 500;
    color: var(--text-dark);
    line-height: 24px;
    letter-spacing: 0.5px;
  }
</style>
</head>
<body>

  <section class="card card-back" aria-label="Business card back">
    <div class="wordmark">PIMLU</div>
    <div class="site">www.<span class="accent">pimlu</span>.com</div>
  </section>

  <section class="card card-front" aria-label="Business card front">
    <svg class="backdrop" viewBox="0 0 700 400" width="700" height="400">
      <circle cx="610" cy="230" r="245" fill="var(--ink)"/>
      <path d="M 535 50 A 200 200 0 0 0 505 385 A 235 235 0 0 1 535 50 Z" fill="var(--brand-red)"/>
      <circle cx="560" cy="220" r="92" fill="var(--paper)"/>
      <circle cx="560" cy="220" r="86" fill="#7f8a78" role="img" aria-label="Portrait photo of the agent">
      </circle>
      <defs>
        <radialGradient id="portraitTone" cx="50%" cy="40%" r="60%">
          <stop offset="0%" stop-color="#c9b6a3"/>
          <stop offset="60%" stop-color="#8a9480"/>
          <stop offset="100%" stop-color="#3b4a3a"/>
        </radialGradient>
      </defs>
      <circle cx="560" cy="220" r="86" fill="url(#portraitTone)" role="img" aria-label="Portrait photo of the agent"/>
    </svg>

    <div class="wordmark">PIMLU</div>

    <div class="agent">
      <div class="agent-name">DANE HOLLOWAY</div>
      <div class="agent-title">Licenced Real Estate Agent</div>
    </div>

    <ul class="contact-list">
      <li>
        <svg viewBox="0 0 16 16" aria-hidden="true"><path d="M3.5 1.5 L6 1.5 L7 5 L5.3 6.3 C6.2 8.2 7.8 9.8 9.7 10.7 L11 9 L14.5 10 L14.5 12.5 C14.5 13.6 13.6 14.5 12.5 14.5 C6.5 14.5 1.5 9.5 1.5 3.5 C1.5 2.4 2.4 1.5 3.5 1.5 Z" fill="var(--brand-red)"/></svg>
        0400 555 318
      </li>
      <li>
        <svg viewBox="0 0 16 16" aria-hidden="true"><rect x="1.5" y="3.5" width="13" height="9" fill="none" stroke="var(--brand-red)" stroke-width="1.5"/><path d="M1.5 3.5 L8 9 L14.5 3.5" fill="none" stroke="var(--brand-red)" stroke-width="1.5"/></svg>
        dane@pimlu.com
      </li>
      <li>
        <svg viewBox="0 0 16 16" aria-hidden="true"><circle cx="8" cy="8" r="6.5" fill="none" stroke="var(--brand-red)" stroke-width="1.3"/><ellipse cx="8" cy="8" rx="3" ry="6.5" fill="none" stroke="var(--brand-red)" stroke-width="1.2"/><path d="M1.5 8 H14.5 M2.5 5 H13.5 M2.5 11 H13.5" stroke="var(--brand-red)" stroke-width="1.1"/></svg>
        www.pimlu.com
      </li>
    </ul>

    <p class="address">PO Box 1190<br>Larkfield NSW 2790</p>
  </section>

</body>
</html>
```